Silver Harbor Staffing Agency

I need to make a brochure/catalogue that represent our company, telling our clients what we do, our values, fields of industry that we taken care of, so they know who we are, what we did, and how we do it.
I do have a logo and simple brochure design before that i really need to upgrade (i will give it as an example on this attachment).

What I want in the new design is :
1. More pictures and little bit of explanation in each industry we work with.
2. Attractive design that make people LOOK at the brochure and not just throw it in the trash.
3. Still use the combination color of the company logo itself, which is Golden Brown.

```html
<!DOCTYPE html>
<html lang="en">
<head>
<meta charset="utf-8">
<title>Silver Harbor Staffing Agency – Brochure</title>
<link href="https://fonts.googleapis.com/css2?family=Montserrat:wght@400;500;600;700;800&display=swap" rel="stylesheet">
<style>
  :root {
    --ink: #1c1b19;
    --ink-soft: #262521;
    --gold: #b18d3c;
    --gold-light: #caa452;
    --gold-deep: #5b3d12;
    --paper: #ffffff;
    --copy: #d9d6cf;
    --stage: #e7e7e7;
    --map-fill: #f1ede4;
  }
  * { margin: 0; padding: 0; box-sizing: border-box; }
  html, body { width: 1200px; height: 3000px; overflow: hidden; }
  body {
    background: var(--stage);
    font-family: "Montserrat", sans-serif;
    color: var(--paper);
    position: relative;
  }
  .spread {
    position: absolute;
    left: 40px;
    width: 1120px;
    height: 840px;
    background: var(--ink);
    overflow: hidden;
    box-shadow: 0 18px 40px rgba(0,0,0,.18);
  }
  .spread--outer { top: 560px; }
  .spread--inner { top: 1640px; }
  .spread__fold {
    position: absolute; left: 559px; top: 0; width: 2px; height: 100%;
    background: rgba(0,0,0,.25);
  }
  .shapes { position: absolute; inset: 0; }
  .block { position: absolute; }
  .section-title {
    font-weight: 700; font-size: 13px; letter-spacing: .06em;
    text-transform: uppercase; color: var(--gold-light); margin-bottom: 8px;
  }
  .section-title--light { color: var(--paper); }
  .section-title--deep { color: var(--gold-deep); }
  .body-copy {
    font-size: 9.5px; line-height: 1.5; color: var(--copy); font-weight: 400;
  }
  .body-copy--dark { color: #2a2015; }
  .photo {
    position: absolute;
    border: 4px solid var(--paper);
  }
  .brand-name {
    font-weight: 700; color: var(--gold-light); letter-spacing: .12em;
    text-transform: uppercase; text-align: center;
  }

  /* outer spread */
  .brand-name--cover { left: 690px; top: 70px; width: 180px; font-size: 20px; line-height: 1.25; }
  .cover-title {
    left: 621px; top: 640px; font-weight: 800; font-size: 34px; line-height: 40px;
    text-transform: uppercase; letter-spacing: .04em;
  }
  .cover-title .accent { color: var(--gold-light); }
  .cover-url { left: 621px; top: 776px; font-size: 11px; font-weight: 600; color: var(--paper); }
  .location-title { left: 38px; top: 246px; }
  .location-map {
    left: 130px; top: 282px; width: 215px; height: 272px;
    background: var(--map-fill); border-radius: 6px;
  }
  .states {
    left: 368px; top: 282px; font-weight: 700; font-size: 12px; line-height: 17px;
  }
  .brand-name--back { left: 30px; top: 604px; font-size: 14px; text-align: left; }
  .contact-form { left: 35px; top: 668px; width: 200px; }
  .contact-info { left: 268px; top: 668px; width: 270px; }
  .phone-line { font-weight: 700; font-size: 15px; display: flex; align-items: center; gap: 8px; margin-bottom: 6px; }
  .info-line { display: flex; align-items: flex-start; gap: 8px; font-size: 9.5px; line-height: 1.45; color: var(--copy); margin-bottom: 6px; }
  .icon { width: 12px; height: 12px; flex: none; margin-top: 1px; }

  /* inner spread */
  .mission-band { position: absolute; left: 0; top: 325px; width: 560px; height: 170px; background: var(--gold); }
  .closing-band { position: absolute; left: 560px; top: 780px; width: 560px; height: 60px; background: var(--gold); }
  .tagline {
    position: absolute; font-weight: 700; font-size: 24px; letter-spacing: .06em; text-transform: uppercase;
  }
  .tagline--left { left: 35px; top: 784px; }
  .tagline--left .accent { color: var(--gold-light); }
  .tagline--right { left: 610px; top: 795px; color: var(--ink); }
  .industry-name { font-weight: 700; font-size: 11px; color: var(--paper); margin-bottom: 4px; }
</style>
</head>
<body>

<section class="spread spread--outer" aria-label="Brochure back and front cover">
  <svg class="shapes" viewBox="0 0 1120 840" width="1120" height="840" aria-hidden="true">
    <defs>
      <linearGradient id="cityStairs" x1="0" y1="0" x2="0" y2="1">
        <stop offset="0" stop-color="#e9b56c"/>
        <stop offset=".35" stop-color="#b7a08a"/>
        <stop offset=".7" stop-color="#7f8a96"/>
        <stop offset="1" stop-color="#4f6172"/>
      </linearGradient>
    </defs>
    <polygon points="0,198 767,198 583,385 817,569 0,569" fill="#b18d3c"/>
    <polygon points="990,0 1120,0 1120,790 609,385" fill="#b18d3c"/>
  </svg>
  <svg class="shapes" viewBox="0 0 1120 840" width="1120" height="840" role="img" aria-label="Photo: a businessman in a suit climbing wide city stairs toward a sunlit skyline">
    <polygon points="1006,0 1120,0 1120,773 627,385" fill="url(#cityStairs)"/>
  </svg>

  <div class="block" style="left:35px; top:35px; width:490px;">
    <h2 class="section-title">Industries</h2>
    <p class="body-copy">Need industry-leading talent for your organization? Career options that are ideal for your skills and experience? The professionals at Silver Harbor Staffing Agency have the tools and knowledge to help you make the perfect match.</p>
  </div>

  <div class="block location-map" role="img" aria-label="Map of the eastern United States with the served states highlighted"></div>
  <div class="block location-title">
    <h2 class="section-title section-title--light">Our Location</h2>
  </div>
  <ul class="block states" style="list-style:none;">
    <li>New York</li>
    <li>Pennsylvania</li>
    <li>New Jersey</li>
    <li>Delaware</li>
    <li>Virginia</li>
  </ul>

  <div class="block brand-name brand-name--back">Silver Harbor Inc.</div>

  <div class="block contact-form">
    <h2 class="section-title">Contact Form</h2>
    <p class="body-copy">Thank you for choosing Silver Harbor Staffing. If you have temporary jobs you are hiring for, please get in touch with Silver Harbor Staffing. We are able to help with all your staffing and employment needs.</p>
  </div>

  <div class="block contact-info">
    <h2 class="section-title">Contact Info</h2>
    <div class="phone-line">
      <svg class="icon" viewBox="0 0 24 24" aria-hidden="true"><path fill="#caa452" d="M6.6 10.8a15.1 15.1 0 0 0 6.6 6.6l2.2-2.2a1 1 0 0 1 1-.25 11.4 11.4 0 0 0 3.6.57 1 1 0 0 1 1 1V20a1 1 0 0 1-1 1A17 17 0 0 1 3 4a1 1 0 0 1 1-1h3.5a1 1 0 0 1 1 1c0 1.25.2 2.45.57 3.57a1 1 0 0 1-.25 1z"/></svg>
      555-014-2280
    </div>
    <div class="info-line">
      <svg class="icon" viewBox="0 0 24 24" aria-hidden="true"><path fill="#caa452" d="M12 2a7 7 0 0 0-7 7c0 5.2 7 13 7 13s7-7.8 7-13a7 7 0 0 0-7-7zm0 9.5A2.5 2.5 0 1 1 12 6.5a2.5 2.5 0 0 1 0 5z"/></svg>
      <span>48 Alder Lane, Suite 210<br>Brookfield, NJ 08000</span>
    </div>
    <div class="info-line">
      <svg class="icon" viewBox="0 0 24 24" aria-hidden="true"><path fill="#caa452" d="M3 5h18a1 1 0 0 1 1 1v12a1 1 0 0 1-1 1H3a1 1 0 0 1-1-1V6a1 1 0 0 1 1-1zm9 7.5L20 7H4z"/></svg>
      <span>info@silverharborstaffing.com</span>
    </div>
    <div class="info-line">
      <svg class="icon" viewBox="0 0 24 24" aria-hidden="true"><circle cx="12" cy="12" r="9" fill="none" stroke="#caa452" stroke-width="2"/><path d="M3 12h18M12 3c3 3 3 15 0 18M12 3c-3 3-3 15 0 18" fill="none" stroke="#caa452" stroke-width="1.6"/></svg>
      <span>www.silverharborstaffing.com</span>
    </div>
  </div>

  <div class="block brand-name brand-name--cover">Silver Harbor Inc.</div>
  <h1 class="block cover-title">Your<br>Best Way<br>To <span class="accent">Succeed</span></h1>
  <div class="block cover-url">www.silverharborstaffing.com</div>

  <div class="spread__fold"></div>
</section>

<section class="spread spread--inner" aria-label="Brochure inner pages">
  <div class="mission-band"></div>
  <div class="closing-band"></div>

  <div class="block" style="left:35px; top:35px; width:490px;">
    <h2 class="section-title">About Us</h2>
    <p class="body-copy">With more than 18 years of experience Silver Harbor Staffing Agency provided staffing services to a wide array of locations, all throughout Pennsylvania. Through the last few years we have expanded to 5 other states including New York, New Jersey, Delaware, Virginia and Georgia. Our ethics are a critical building block of our business. Our own success is based on adherence to the highest ethical standards, long-term client relationships, the ability to identify top candidates, and the high-quality professional development of Silver Harbor Staffing professionals protecting the confidentiality and interests of clients and candidates.</p>
  </div>

  <div class="block" style="left:35px; top:188px; width:490px;">
    <h2 class="section-title">Culture</h2>
    <p class="body-copy">Silver Harbor Staffing believes in equal opportunity for all, regardless of gender, race, ethnic origin, religion, or landscape. The staffing policies and practices of Silver Harbor Staffing for our organization, our clients and candidates are fully non-discriminatory. Our employees are our most valuable asset. We strive to create a work environment of professionalism, trust and respect that will continuously provide our staff with motivation, challenge, and professional growth to aim our most important goal: CLIENT SATISFACTION.</p>
  </div>

  <div class="block" style="left:35px; top:338px; width:490px;">
    <h2 class="section-title section-title--deep">Mission</h2>
    <p class="body-copy body-copy--dark">Silver Harbor Staffing is more than a staffing company, we want to become your business partner. We understand that payroll and employee service matter.</p>
    <p class="body-copy body-copy--dark" style="margin-top:8px;">Overhead can be one of the largest expenses for your business. Through our partnership network programs Silver Harbor Staffing can help you reduce the hard costs of your business expenses. We take responsibility for all of your placed employees, including payroll taxes and benefits, allowing you to focus on running your business.</p>
  </div>

  <div class="block" style="left:35px; top:518px; width:490px;">
    <h2 class="section-title">Our Process</h2>
    <p class="body-copy">Our screening process includes a thorough interview with each potential candidate to give us insight into the candidate's previous work history, skills, communication abilities and career goals as well as reference checks with their previous employers.</p>
  </div>

  <div class="block" style="left:35px; top:616px; width:280px;">
    <h2 class="section-title">Our Services</h2>
    <p class="body-copy">Silver Harbor Staffing's personalized services, expertise and affordable rates are key factors of our success and being our client's choice staffing agency. Our command and contract-to-hire employees are looking for flexible careers in New York, New Jersey, Pennsylvania, Delaware, Virginia and Georgia.</p>
  </div>
  <div class="photo" role="img" aria-label="Photo: a smiling staffing consultant in a shirt and tie in an office"
       style="left:327px; top:612px; width:198px; height:118px; background:linear-gradient(135deg,#c9b49a,#8c6f55 55%,#4d3e34);"></div>

  <p class="tagline tagline--left">Connecting <span class="accent">Opportunity</span></p>

  <div class="block" style="left:610px; top:35px;">
    <h2 class="section-title">Industries We Serve:</h2>
  </div>

  <div class="block" style="left:610px; top:66px; width:235px;">
    <h3 class="industry-name">Warehousing</h3>
    <p class="body-copy">Warehousing is the act of storing goods that will be sold or distributed later. While a small, home-based business might be warehousing products in a spare room, basement, or garage, larger businesses typically own or rent space in a building that is specifically designed for storage.</p>
  </div>
  <div class="photo" role="img" aria-label="Photo: warehouse worker in a hard hat and safety vest among stocked shelves"
       style="left:870px; top:80px; width:190px; height:100px; background:linear-gradient(135deg,#d8c3a0,#9b7b52 50%,#4a3b2c);"></div>

  <div class="photo" role="img" aria-label="Photo: hotel receptionist at a bright front desk"
       style="left:610px; top:215px; width:150px; height:105px; background:linear-gradient(135deg,#efe6da,#bfa98e 55%,#6f5a47);"></div>
  <div class="block" style="left:855px; top:230px; width:225px;">
    <h3 class="industry-name">Hotel</h3>
    <p class="body-copy">Whether you are travelling for business or pleasure, the luxury hotel services offered by the five-star Harborview Hotel make it an ideal choice for your stay in Riga, Latvia.</p>
  </div>

  <div class="block" style="left:610px; top:368px; width:235px;">
    <h3 class="industry-name">Farming</h3>
    <p class="body-copy">Farming is growing crops or keeping animals by people for food and raw materials. Farming is a part of agriculture.</p>
  </div>
  <div class="photo" role="img" aria-label="Photo: farm worker tending rows of green plants in a greenhouse"
       style="left:870px; top:365px; width:190px; height:100px; background:linear-gradient(135deg,#b7cf7a,#5e8a3a 55%,#2c4220);"></div>

  <div class="photo" role="img" aria-label="Photo: mail room worker sorting packages on a conveyor"
       style="left:610px; top:495px; width:145px; height:103px; background:linear-gradient(135deg,#e2e2e0,#9aa0a6 55%,#4b5058);"></div>
  <div class="block" style="left:830px; top:500px; width:245px;">
    <h3 class="industry-name">Paper Mailling</h3>
    <p class="body-copy">Our paper mailing courier sacks have become popular with businesses and organisations looking for sustainable alternatives to polythene mailing bags.</p>
  </div>

  <div class="block" style="left:610px; top:622px; width:235px;">
    <h3 class="industry-name">Landfill</h3>
    <p class="body-copy">Landfill gas is produced by wet organic waste decomposing under anaerobic conditions in a landfill. Landfill gas production is dependent on the degradation status of the waste material as well as moisture and temperature, all of which may vary greatly in different parts of the landfill body.</p>
  </div>
  <div class="photo" role="img" aria-label="Photo: worker in a red safety vest operating equipment at a landfill site"
       style="left:870px; top:635px; width:190px; height:100px; background:linear-gradient(135deg,#c98a5a,#7a4a34 55%,#3a2a24);"></div>

  <p class="tagline tagline--right">With Today's Top Talent</p>

  <div class="spread__fold"></div>
</section>

</body>
</html>
```